Business card for law firm

Need business card for new law firm. Think confident, authoritative, conservative, but not stuffy or old-fashioned.

Contact Information for Business Card

Content for card - logo (uploaded), plus the following:

Paul Whitcombe (larger font)
Managing Partner (larger font, but not as large as name)
Level 9, 7 Ferris Lane
Sydney NSW 2000
Main Tel 02 9364 2710
Direct Tel 02 8472 3159
Email paul@qvlegal.com.au
www.qvlegal.com.au

Letterhead design should include logo plus:
Level 9, 7 Ferris Lane
Sydney NSW 2000
Tel 02 8472 3159
www.qvlegal.com.au

```html
<!DOCTYPE html>
<html lang="en">
<head>
<meta charset="utf-8">
<title>Quayvale Lawyers – Business Card</title>
<link href="https://fonts.googleapis.com/css2?family=Cormorant+Garamond:wght@500;600&family=Roboto:wght@400&display=swap" rel="stylesheet">
<style>
  :root {
    --navy: #0c2469;
    --ink: #1a1a1a;
    --grey: #6b6b6b;
    --rule: #9a9a9a;
    --paper: #ffffff;
    --stage: #e9e7e3;
  }
  * { margin: 0; padding: 0; box-sizing: border-box; }
  html, body { width: 1200px; height: 768px; overflow: hidden; }
  body {
    background: var(--stage);
    display: flex;
    align-items: center;
    justify-content: center;
    gap: 60px;
    font-family: "Roboto", Arial, sans-serif;
  }
  .card {
    position: relative;
    width: 500px;
    height: 286px;
    box-shadow: 0 8px 24px rgba(0,0,0,.18);
  }
  .card--front { background: var(--paper); }
  .card--back { background: var(--navy); color: #fff; }

  .person { position: absolute; left: 34px; top: 40px; }
  .person__name {
    font-family: "Cormorant Garamond", "Times New Roman", serif;
    font-weight: 500; font-size: 27px; letter-spacing: .5px;
    color: var(--navy); text-transform: uppercase; line-height: 1;
  }
  .person__role {
    font-family: "Cormorant Garamond", "Times New Roman", serif;
    font-weight: 600; font-size: 15px; color: var(--ink);
    text-transform: uppercase; margin-top: 4px;
  }

  .contact {
    position: absolute; left: 34px; bottom: 38px;
    list-style: none; font-size: 12.5px; color: var(--grey); line-height: 1.38;
  }
  .contact__item { display: flex; align-items: center; gap: 8px; }
  .contact__icon { width: 11px; height: 11px; fill: var(--navy); flex: none; }

  .rule {
    position: absolute; left: 34px; right: 28px; bottom: 28px;
    height: 1px; background: var(--rule);
  }

  .wordmark {
    position: absolute;
    display: flex; align-items: center; gap: 10px;
  }
  .wordmark__square {
    width: 16px; height: 16px; background: var(--navy); flex: none;
  }
  .wordmark__name {
    font-family: "Roboto", Arial, sans-serif;
    font-weight: 400; font-size: 22px; line-height: 1;
    color: var(--ink); white-space: nowrap;
  }
  .card--front .wordmark { right: 30px; bottom: 42px; }

  .card--back .wordmark { left: 36px; bottom: 66px; }
  .card--back .wordmark__square { background: #fff; }
  .card--back .wordmark__name { color: #fff; font-size: 26px; }
  .back__url {
    position: absolute; left: 36px; bottom: 38px;
    font-family: "Roboto", Arial, sans-serif;
    font-weight: 400; font-size: 13px; color: #fff;
  }
</style>
</head>
<body>
  <section class="card card--front" aria-label="Business card front">
    <div class="person">
      <p class="person__name">Paul Whitcombe</p>
      <p class="person__role">Managing Partner</p>
    </div>

    <ul class="contact">
      <li class="contact__item">Level 9, 7 Ferris Lane</li>
      <li class="contact__item">Sydney NSW 2000</li>
      <li class="contact__item">
        <svg class="contact__icon" viewBox="0 0 24 24" aria-hidden="true"><path d="M6.6 10.8a15 15 0 0 0 6.6 6.6l2.2-2.2a1 1 0 0 1 1-.25 11.4 11.4 0 0 0 3.6.57 1 1 0 0 1 1 1V20a1 1 0 0 1-1 1A17 17 0 0 1 3 4a1 1 0 0 1 1-1h3.5a1 1 0 0 1 1 1c0 1.25.2 2.45.57 3.57a1 1 0 0 1-.25 1z"/></svg>
        02 9364 2710</li>
      <li class="contact__item">
        <svg class="contact__icon" viewBox="0 0 24 24" aria-hidden="true"><path d="M6.6 10.8a15 15 0 0 0 6.6 6.6l2.2-2.2a1 1 0 0 1 1-.25 11.4 11.4 0 0 0 3.6.57 1 1 0 0 1 1 1V20a1 1 0 0 1-1 1A17 17 0 0 1 3 4a1 1 0 0 1 1-1h3.5a1 1 0 0 1 1 1c0 1.25.2 2.45.57 3.57a1 1 0 0 1-.25 1z"/></svg>
        02 8472 3159</li>
      <li class="contact__item">
        <svg class="contact__icon" viewBox="0 0 24 24" aria-hidden="true"><path d="M2 5h20v14H2z M3.5 6.5 12 13l8.5-6.5" stroke="#fff" stroke-width="1.6"/></svg>
        paul@qvlegal.com.au</li>
      <li class="contact__item">
        <svg class="contact__icon" viewBox="0 0 24 24" aria-hidden="true"><circle cx="12" cy="12" r="11"/><path d="M1 12h22M12 1c4 4 4 18 0 22M12 1c-4 4-4 18 0 22" stroke="#fff" stroke-width="1.4" fill="none"/></svg>
        www.qvlegal.com.au</li>
    </ul>

    <div class="wordmark">
      <span class="wordmark__square" aria-hidden="true"></span>
      <p class="wordmark__name">Quayvale Lawyers</p>
    </div>

    <div class="rule" aria-hidden="true"></div>
  </section>

  <section class="card card--back" aria-label="Business card back">
    <div class="wordmark">
      <span class="wordmark__square" aria-hidden="true"></span>
      <p class="wordmark__name">Quayvale Lawyers</p>
    </div>
    <p class="back__url">www.qvlegal.com.au</p>
  </section>
</body>
</html>
```